Brell Stone Company Business Cards

Front and Back Business Card - logo and text setup - cool design. I need workable photoshop or illustrator files so I can setup each employee card with design that is created
Updates

Hi everyone, thank you for the great entries. Please no more white and blue cards - there are so many already - black and silver only now please. thanks!

Target Market(s)

Construction Industry - Facility Managers

Industry/Entity Type

Construction

Contact Information for Business Card

I really like contemporary simplistic looks - clean neat....not opposed to seeing some black backrounds

Requirements
Must have
• Logo/website address with design on front only - www.brellstone-example.com (logo attached)
• Back:
• Name/Title/Company Address/Phone/email address
Nice to have
• Cool design
Should not have
• Nothing gimmicky like Fire or Water - since we are a Fire Protection company - it has all been done

```html
<!DOCTYPE html>
<html lang="en">
<head>
<meta charset="utf-8">
<title>Brell Stone Company Business Cards</title>
<link rel="stylesheet" href="https://fonts.googleapis.com/css2?family=Montserrat:wght@400;600;800&display=swap">
<style>
  :root {
    --bg: #e9e8e6;
    --silver-light: #f1f2f3;
    --silver: #c9ccd0;
    --silver-mid: #a7abb0;
    --graphite: #3a3b3d;
    --black: #111111;
    --black-soft: #2a2b2d;
    --ink: #4a4b4d;
  }
  * { margin: 0; padding: 0; box-sizing: border-box; }
  html, body { width: 1200px; height: 866px; overflow: hidden; }
  body {
    background: var(--bg);
    font-family: "Montserrat", Arial, sans-serif;
    position: relative;
  }
  .card {
    position: absolute;
    width: 540px;
    height: 309px;
    box-shadow: 0 10px 24px rgba(0,0,0,0.22);
    overflow: hidden;
  }
  /* Contact side */
  .card-contact {
    left: 60px; top: 70px;
    background: linear-gradient(135deg, var(--silver-light) 0%, #dfe1e4 100%);
  }
  .card-contact .edge-band { position: absolute; left: 0; top: 0; width: 70px; height: 309px; }
  .card-contact .person { position: absolute; left: 92px; top: 40px; }
  .person-name { color: var(--black); font-size: 27px; font-weight: 600; letter-spacing: 0.5px; }
  .person-title { color: var(--ink); font-size: 17px; font-weight: 400; margin-top: 2px; }
  .address {
    position: absolute; right: 34px; top: 120px;
    text-align: right; color: var(--ink); font-size: 12.5px; line-height: 1.5;
  }
  .contacts {
    position: absolute; left: 92px; bottom: 34px;
    color: var(--ink); font-size: 13px; line-height: 1.7;
  }
  .icons { position: absolute; left: 24px; bottom: 38px; display: flex; flex-direction: column; gap: 8px; }
  /* Brand side */
  .card-brand {
    left: 600px; top: 480px;
    background: radial-gradient(ellipse at 30% 20%, var(--black-soft), var(--black) 85%);
  }
  .brand-mark {
    position: absolute; left: 0; right: 0; top: 108px;
    display: flex; justify-content: center; align-items: center; gap: 14px;
  }
  .brand-square { width: 22px; height: 22px; background: var(--silver-mid); }
  .brand-name { color: var(--silver); font-size: 44px; font-weight: 800; letter-spacing: -0.5px; }
  .website {
    position: absolute; left: 0; right: 0; bottom: 52px;
    text-align: center; color: var(--silver); font-size: 15px; font-weight: 600; letter-spacing: 1.5px;
  }
</style>
</head>
<body>
  <section class="card card-contact">
    <svg class="edge-band" viewBox="0 0 70 309" aria-hidden="true">
      <polygon points="0,0 45,0 70,140 70,150 0,190" fill="var(--silver-mid)"/>
      <polygon points="70,162 70,309 0,309 0,204" fill="var(--black)"/>
    </svg>
    <div class="person">
      <div class="person-name">Dana Reyes</div>
      <div class="person-title">Manager</div>
    </div>
    <div class="address">
      <div>48 Quarry Lane</div>
      <div>Ridgeton, AB, T0A 0A0</div>
    </div>
    <div class="icons" aria-hidden="true">
      <svg width="14" height="14" viewBox="0 0 24 24"><path fill="var(--silver)" d="M6.6 10.8a15 15 0 0 0 6.6 6.6l2.2-2.2c.3-.3.7-.4 1-.2 1.1.4 2.3.6 3.6.6.6 0 1 .4 1 1V20c0 .6-.4 1-1 1A17 17 0 0 1 3 4c0-.6.4-1 1-1h3.5c.6 0 1 .4 1 1 0 1.3.2 2.5.6 3.6.1.3 0 .7-.2 1z"/></svg>
      <svg width="14" height="12" viewBox="0 0 24 18"><rect x="1" y="1" width="22" height="16" fill="var(--silver)"/><path d="M1 1l11 9 11-9" fill="none" stroke="var(--black)" stroke-width="2"/></svg>
    </div>
    <div class="contacts">
      <div>123-555-0142</div>
      <div>dana.reyes@brellstone-example.com</div>
    </div>
  </section>

  <section class="card card-brand">
    <div class="brand-mark">
      <span class="brand-square"></span>
      <span class="brand-name">Brell Stone</span>
    </div>
    <div class="website">www.brellstone-example.com</div>
  </section>
</body>
</html>
```